Construction material supplies company business card ****

1. Full company name “K T Masonry Works Ltd”
I am after a Business card design for the company as a whole. We are better known in Solomon Islands as “K T Masonry” for short.

We are a building materials supplier of
Ready Mixed Concrete, Bricks and Blocks,
Quarry products- gravel, aggregates, sand etc.
Cement distributor/retailer of reputable brands.
Other prefab concrete products. Culverts, wave breakers, concrete retaining blocks etc.

2. Competitive Advantage over Competition: Quality, efficient, professional, dependable, reliable

3. We want people to feel trust worthy, high quality, strong when they see our brand

5. No preference to color. Maybe more sturdy and corporate. Not fancy.

Industry/Entity Type

CONSTRUCTION SUPPLY

Contact Information for Business Card

Name, Position, office phone mob phone, email

Requirements
Must have
• the company logo
Nice to have
• would like to see a mixture of designs, of with logo only and also with simple graphic designs to bring out the company whilst still have the strong sturdy professional feeling

```html
<!DOCTYPE html>
<html lang="en">
<head>
<meta charset="utf-8">
<title>K T Masonry – Business Card</title>
<link href="https://fonts.googleapis.com/css2?family=Arimo:wght@400;700&display=swap" rel="stylesheet">
<style>
  :root {
    --backdrop: #ebebe9;
    --navy: #1d4569;
    --navy-dark: #14304b;
    --navy-light: #356590;
    --white: #ffffff;
    --rule: rgba(255,255,255,0.85);
  }
  * { margin: 0; padding: 0; box-sizing: border-box; }
  html, body {
    width: 1200px; height: 801px; overflow: hidden;
    background: var(--backdrop);
    font-family: "Arimo", Arial, sans-serif;
  }
  .stage {
    position: relative; width: 1200px; height: 801px;
    display: flex; align-items: center; justify-content: center; gap: 40px;
  }
  .card {
    position: relative; width: 540px; height: 310px;
    background: var(--navy); color: var(--white);
    box-shadow: 0 6px 18px rgba(0,0,0,0.18);
    overflow: hidden;
  }
  .brand {
    position: absolute; display: flex; align-items: center; gap: 12px;
    white-space: nowrap;
  }
  .brand-mark { flex: none; background: var(--white); }
  .brand-name { font-weight: 700; letter-spacing: 1px; line-height: 1; }

  /* front */
  .card-front .brand { right: 36px; top: 44px; }
  .card-front .brand-mark { width: 30px; height: 30px; }
  .card-front .brand-name { font-size: 30px; }
  .card-front .divider {
    position: absolute; left: 36px; right: 36px; top: 168px;
    height: 1px; background: var(--rule);
  }
  .person { position: absolute; left: 36px; top: 118px; }
  .person-name { font-weight: 700; font-size: 20px; letter-spacing: 0.3px; line-height: 1; }
  .person-role { font-size: 14px; margin-top: 5px; line-height: 1; }
  .contacts { position: absolute; left: 36px; top: 188px; list-style: none; }
  .contacts li {
    display: flex; align-items: center; gap: 10px;
    font-size: 15px; line-height: 1; margin-bottom: 11px;
  }
  .contacts svg { width: 14px; height: 14px; flex: none; }
  .address {
    position: absolute; right: 36px; top: 192px;
    font-size: 14px; line-height: 1.35; text-align: right;
  }

  /* back */
  .back-decoration {
    position: absolute; left: 0; top: 40px; width: 290px; height: 270px;
    background: linear-gradient(135deg, var(--navy-dark) 0%, var(--navy) 45%, var(--navy-light) 100%);
    opacity: 0.85;
  }
  .card-back .brand { right: 32px; bottom: 44px; }
  .card-back .brand-name { font-size: 36px; }
</style>
</head>
<body>
<main class="stage">
  <section class="card card-front" aria-label="Business card front">
    <div class="brand">
      <span class="brand-mark" aria-hidden="true"></span>
      <p class="brand-name">K T Masonry</p>
    </div>
    <div class="person">
      <p class="person-name">DANIEL REEVE</p>
      <p class="person-role">Manager</p>
    </div>
    <div class="divider"></div>
    <ul class="contacts">
      <li>
        <svg viewBox="0 0 16 16" aria-hidden="true"><path fill="#fff" d="M4 1.5 6.2 4 5 5.6c.9 2 2.4 3.5 4.4 4.4L11 8.8l2.5 2.2-1.4 2.6C6.6 13.3 2.7 9.4 1.4 3.9z"/></svg>
        677-745-2100
      </li>
      <li>
        <svg viewBox="0 0 16 16" aria-hidden="true"><rect x="1" y="3" width="14" height="10" fill="#fff"/><path d="M1 3l7 5.5L15 3" fill="none" stroke="#1d4569" stroke-width="1.3"/></svg>
        office@ktmasonry.sb
      </li>
      <li>
        <svg viewBox="0 0 16 16" aria-hidden="true"><circle cx="8" cy="8" r="6.5" fill="none" stroke="#fff" stroke-width="1.5"/><path d="M1.5 8h13M8 1.5c3 3 3 10 0 13M8 1.5c-3 3-3 10 0 13" fill="none" stroke="#fff" stroke-width="1.2"/></svg>
        www.ktmasonry.sb
      </li>
    </ul>
    <p class="address">Your address, city<br>state, ZIP 0000</p>
  </section>

  <section class="card card-back" aria-label="Business card back">
    <div class="back-decoration" role="img" aria-label="Large embossed brand symbol decoration in tones of navy"></div>
    <div class="brand">
      <p class="brand-name">K T Masonry</p>
    </div>
  </section>
</main>
</body>
</html>
```